Moravel Aesthetic Doctor

I require an elegant, luxurious looking business card for my aesthetic business. I am a doctor and that will set me aside from competitors. I am planning to provide home and spa based treatments to clients with high expectations. I have attached my logo.

```html
<!DOCTYPE html>
<html lang="en">
<head>
<meta charset="utf-8">
<title>Moravel Aesthetic Doctor – Business Card</title>
<link href="https://fonts.googleapis.com/css2?family=Montserrat:wght@300;400;500&display=swap" rel="stylesheet">
<style>
  :root {
    --backdrop: #1b1b1d;
    --card-dark: #3b3b3d;
    --card-light: #ffffff;
    --ring-grey: #a7a8ab;
    --text-light: #e6e6e8;
    --text-soft: #c9c9cc;
    --accent-blue: #2a9fe0;
  }
  * { box-sizing: border-box; margin: 0; padding: 0; }
  html, body {
    width: 1200px; height: 786px; overflow: hidden;
    background: var(--backdrop);
    font-family: "Montserrat", sans-serif;
  }
  .canvas {
    width: 1200px; height: 786px;
    display: flex; flex-direction: column;
    align-items: center; justify-content: center; gap: 40px;
  }
  .card {
    width: 600px; height: 343px;
    background: var(--card-dark);
    position: relative; overflow: hidden;
    box-shadow: 0 10px 30px rgba(0,0,0,.5);
  }

  /* Front */
  .front__panel {
    position: absolute; left: 0; top: 0; bottom: 0; width: 265px;
    background: var(--card-light);
    clip-path: ellipse(265px 240px at 0 50%);
  }
  .front__panel svg { position: absolute; left: 0; top: 0; }
  .brand {
    display: flex; align-items: center; gap: 10px;
    color: var(--text-light); font-weight: 300;
  }
  .brand__circle {
    border: 2px solid var(--ring-grey); border-radius: 50%; flex: none;
  }
  .front .brand {
    position: absolute; right: 28px; top: 30px;
    font-size: 15px; letter-spacing: 2px; text-transform: uppercase;
  }
  .front .brand__circle { width: 34px; height: 34px; }
  .contact {
    position: absolute; right: 28px; top: 118px;
    text-align: right;
  }
  .contact__name { color: var(--accent-blue); font-weight: 500; font-size: 15px; margin-bottom: 6px; }
  .contact__title { color: var(--text-soft); font-size: 12px; line-height: 1.45; font-weight: 400; }
  .contact__list { list-style: none; margin-top: 22px; }
  .contact__list li {
    color: var(--text-light); font-size: 12px; line-height: 1.9;
    display: flex; align-items: center; justify-content: flex-end; gap: 8px;
  }
  .contact__list svg { width: 11px; height: 11px; fill: none; stroke: var(--accent-blue); stroke-width: 2; }

  /* Back */
  .back .brand {
    position: absolute; left: 50%; top: 70px; transform: translateX(-50%);
    font-size: 26px; letter-spacing: 4px; text-transform: uppercase; white-space: nowrap;
  }
  .back .brand__circle { width: 62px; height: 62px; }
  .services {
    position: absolute; left: 0; right: 0; top: 190px;
    text-align: center; color: var(--text-light);
    font-size: 14px; line-height: 1.7; font-weight: 400;
  }
  .services .sep { color: var(--accent-blue); padding: 0 6px; }
  .services__tagline { letter-spacing: 1px; text-transform: uppercase; font-size: 13px; }
</style>
</head>
<body>
<main class="canvas">
  <section class="card front">
    <div class="front__panel" role="img" aria-label="Large decorative brand area on white">
      <svg width="265" height="343" viewBox="0 0 265 343">
        <circle cx="110" cy="171" r="118" fill="none" stroke="#a7a8ab" stroke-width="5"/>
      </svg>
    </div>
    <div class="brand"><span class="brand__circle"></span><span>Moravel Aesthetic Doctor</span></div>
    <div class="contact">
      <p class="contact__name">Dr Elise Marden MRCPCH MD</p>
      <p class="contact__title">Australasian Diploma<br>of Aesthetic Medicine</p>
      <ul class="contact__list">
        <li>0800 555 014
          <svg viewBox="0 0 12 12"><path d="M2 1.5l2 0 1 3-1.5 1a6 6 0 0 0 3 3l1-1.5 3 1v2c-5 0.5-9-3.5-8.5-8.5z"/></svg></li>
        <li>elise@moravel.co.nz
          <svg viewBox="0 0 12 12"><rect x="1" y="2.5" width="10" height="7"/><path d="M1 2.5l5 4 5-4"/></svg></li>
        <li>www.moravel.co.nz
          <svg viewBox="0 0 12 12"><circle cx="6" cy="6" r="5"/><path d="M1 6h10M6 1c-2.5 3-2.5 7 0 10M6 1c2.5 3 2.5 7 0 10"/></svg></li>
      </ul>
    </div>
  </section>

  <section class="card back">
    <div class="brand"><span class="brand__circle"></span><span>Moravel Aesthetic Doctor</span></div>
    <div class="services">
      <p>Dermal injectables<span class="sep">|</span>Plasma facials<span class="sep">|</span>Microneedling</p>
      <p>Skin boosters<span class="sep">|</span>Excessive sweating</p>
      <p class="services__tagline">Home and spa based treatments</p>
    </div>
  </section>
</main>
</body>
</html>
```